MRT Property - Business Cards

Looking for a business card & general letterhead, signage etc design for our new logo.

Colours:
000a20
0056a2
00b5ef
0088ce
68cef2

Fonts:
Poppins
Karla

Please keep look and feel of new brand - example in the zip package I sent.

```html
<!DOCTYPE html>
<html lang="en">
<head>
<meta charset="utf-8">
<title>MRT Property – Business Cards</title>
<link href="https://fonts.googleapis.com/css2?family=Poppins:wght@400;500;600&family=Neucha&display=swap" rel="stylesheet">
<style>
  :root {
    --navy: #000a20;
    --card-dark: #121829;
    --blue-deep: #0056a2;
    --blue-mid: #0088ce;
    --blue-bright: #00b5ef;
    --blue-light: #68cef2;
    --ink: #1b1b1b;
    --paper: #ffffff;
    --backdrop: #e9ecf0;
  }
  * { margin: 0; padding: 0; box-sizing: border-box; }
  html, body { width: 900px; height: 1200px; overflow: hidden; }
  body {
    background: var(--backdrop);
    font-family: "Poppins", sans-serif;
    position: relative;
  }
  .card {
    position: absolute;
    left: 80px;
    width: 742px;
    height: 441px;
    border-radius: 22px;
    overflow: hidden;
    box-shadow: 0 6px 18px rgba(0, 10, 32, 0.18);
  }
  .card--front { top: 131px; background: var(--paper); }
  .card--back { top: 638px; background: var(--card-dark); }

  .wordmark {
    position: absolute;
    font-family: "Poppins", sans-serif;
    font-weight: 600;
    white-space: nowrap;
    display: flex;
    align-items: center;
  }
  .wordmark__dot { border-radius: 50%; flex: none; }
  .card--front .wordmark {
    left: 70px; top: 192px;
    font-size: 36px; color: var(--blue-deep);
  }
  .card--front .wordmark__dot {
    width: 26px; height: 26px; margin-right: 14px; background: var(--blue-bright);
  }
  .card--back .wordmark {
    left: 0; right: 0; top: 168px; justify-content: center;
    font-size: 72px; color: var(--paper);
  }
  .card--back .wordmark__dot {
    width: 56px; height: 56px; margin-right: 26px; background: var(--blue-mid);
  }

  .divider {
    position: absolute; left: 355px; top: 109px;
    width: 2px; height: 224px; background: var(--blue-deep);
  }
  .contact { position: absolute; left: 372px; top: 106px; color: var(--ink); }
  .contact__name {
    font-family: "Neucha", cursive;
    font-size: 34px; line-height: 1; color: var(--blue-deep);
  }
  .contact__role { font-size: 15px; margin-top: 9px; }
  .contact__address { font-size: 15px; line-height: 21px; margin-top: 23px; }
  .contact__list { list-style: none; margin-top: 23px; }
  .contact__list li {
    display: flex; align-items: center;
    font-size: 15px; height: 28px;
  }
  .contact__list svg { width: 15px; height: 15px; margin-right: 11px; fill: var(--blue-deep); }

  .colour-band {
    position: absolute; left: 0; bottom: 0; width: 100%; height: 19px; display: flex;
  }
  .colour-band span { flex: 1; }
  .colour-band .c1 { background: var(--blue-light); }
  .colour-band .c2 { background: var(--blue-bright); }
  .colour-band .c3 { background: var(--blue-mid); }
  .colour-band .c4 { background: var(--blue-deep); }
</style>
</head>
<body>
  <section class="card card--front" aria-label="Business card front">
    <div class="wordmark"><span class="wordmark__dot"></span>MRT Property</div>
    <div class="divider"></div>
    <div class="contact">
      <p class="contact__name">Daniel Harper</p>
      <p class="contact__role">Mnaging Director</p>
      <p class="contact__address">412 Birch Hollow Rd Suite<br>220 Dayton Ohio 45402</p>
      <ul class="contact__list">
        <li>
          <svg viewBox="0 0 24 24" aria-hidden="true"><path d="M6.6 10.8a15.1 15.1 0 0 0 6.6 6.6l2.2-2.2a1 1 0 0 1 1-.25 11.4 11.4 0 0 0 3.6.57 1 1 0 0 1 1 1V20a1 1 0 0 1-1 1A17 17 0 0 1 3 4a1 1 0 0 1 1-1h3.5a1 1 0 0 1 1 1c0 1.25.2 2.45.57 3.57a1 1 0 0 1-.25 1z"/></svg>
          1 (555) 014-2736
        </li>
        <li>
          <svg viewBox="0 0 24 24" aria-hidden="true"><path d="M2 5h20v14H2z M2 5l10 7 10-7" fill="none" stroke="#0056a2" stroke-width="0"/><path d="M2 6.5V19h20V6.5l-10 7z M2.5 5h19L12 11.6z"/></svg>
          info@mrtproperty.com
        </li>
        <li>
          <svg viewBox="0 0 24 24" aria-hidden="true"><path d="M12 2a10 10 0 1 0 0 20 10 10 0 0 0 0-20zm-1 17.9A8 8 0 0 1 4 12l1-.9 4 4v1a2 2 0 0 0 2 2zm6.9-2.5A2 2 0 0 0 16 16h-1v-3a1 1 0 0 0-1-1H8v-2h2a1 1 0 0 0 1-1V7h2a2 2 0 0 0 2-2v-.4a8 8 0 0 1 2.9 12.8z"/></svg>
          www.mrtproperty.com
        </li>
      </ul>
    </div>
    <div class="colour-band"><span class="c1"></span><span class="c2"></span><span class="c3"></span><span class="c4"></span></div>
  </section>

  <section class="card card--back" aria-label="Business card back">
    <div class="wordmark"><span class="wordmark__dot"></span>MRT Property</div>
  </section>
</body>
</html>
```